Retail Jewelry Business Card Design Project

We are in need of a new business card design for a retail jewelry store. This store is in the business of fine jewelry including but not specific to bridal jewelry, diamonds, designer jewelry and watches.

This store has been in business for 20 years but continues to strive for a modern professional appeal. The main colors use for this business are a royal blue, white and silver.

Target Market(s)

Target market is ages 18-50

Industry/Entity Type

Jewelry

Requirements
Must have
• Sales Person Name
Sales Person Email Address

Store Address
Store Phone
Website

Standard business card size. No odd shapes or sizes.
Nice to have
• Overall modern feel for card.

We have thought that a design with a nice feature of the logo on the back of the card would be nice but open to ideas.
Should not have
• No specific images of jewelry should be used.

```html
<!DOCTYPE html>
<html lang="en">
<head>
<meta charset="utf-8">
<title>Marlowe Hale Fine Jewelry – Business Card Set</title>
<link rel="stylesheet" href="https://fonts.googleapis.com/css2?family=Open+Sans:ital,wght@0,400;0,600;0,700;1,700&display=swap">
<style>
  :root {
    --royal: #2d3192;
    --lavender: #7570b3;
    --navy: #25286e;
    --white: #ffffff;
    --stage: #a87a50;
    --label: #1c1c1c;
    --ink: #2b2b2b;
  }
  * { margin: 0; padding: 0; box-sizing: border-box; }
  html, body { width: 1200px; height: 788px; overflow: hidden; }
  body {
    background: var(--stage);
    font-family: "Open Sans", Arial, sans-serif;
    position: relative;
  }
  .sheet-label {
    position: absolute;
    width: 525px;
    text-align: center;
    font-size: 20px;
    color: var(--label);
  }
  .card {
    position: absolute;
    width: 525px;
    height: 300px;
    border-radius: 22px;
    overflow: hidden;
    box-shadow: 0 4px 10px rgba(0,0,0,0.35);
  }
  .card--white { background: var(--white); }
  .card--royal { background: var(--royal); }
  .card--lavender { background: var(--lavender); }

  /* Front */
  .front-wave { position: absolute; left: 0; top: 0; width: 525px; height: 120px; }
  .holder-name {
    position: absolute; right: 25px; top: 30px;
    color: var(--white); font-size: 16px;
  }
  .front-brand {
    position: absolute; left: 32px; top: 100px;
    color: var(--royal); font-weight: 700;
  }
  .front-brand .brand-name { font-size: 30px; line-height: 1.1; }
  .front-brand .brand-line { font-size: 14px; letter-spacing: 1.5px; margin-top: 4px; }
  .address {
    position: absolute; left: 30px; top: 242px;
    font-size: 13px; line-height: 17px; color: var(--ink);
  }
  .contact {
    position: absolute; right: 25px; top: 211px;
    text-align: right; font-size: 13px; line-height: 23.5px; color: var(--ink);
    list-style: none;
  }
  .contact b { font-style: italic; font-weight: 700; }

  /* Backs */
  .back-brand {
    position: absolute; left: 0; right: 0; top: 78px;
    text-align: center; font-weight: 700;
  }
  .back-brand .brand-name { font-size: 52px; line-height: 1.1; }
  .back-brand .brand-line { font-size: 20px; letter-spacing: 2px; margin-top: 6px; }
  .back-web {
    position: absolute; left: 0; right: 0; top: 259px;
    text-align: center; font-size: 13px; letter-spacing: 2px;
  }
  .card--white .back-brand, .card--white .back-web { color: var(--royal); }
  .card--royal .back-brand, .card--royal .back-web { color: var(--white); }
  .card--lavender .back-brand { color: var(--navy); }
  .card--lavender .back-web { color: var(--navy); }
</style>
</head>
<body>
  <p class="sheet-label" style="left:55px; top:33px;">Front</p>
  <p class="sheet-label" style="left:621px; top:33px;">Back - 1</p>
  <p class="sheet-label" style="left:54px; top:403px;">Back - 2</p>
  <p class="sheet-label" style="left:622px; top:403px;">Back - 3</p>

  <section class="card card--white card-front" style="left:55px; top:73px;">
    <svg class="front-wave" viewBox="0 0 525 120" aria-hidden="true">
      <path d="M0 52 C90 38 170 36 260 60 C350 84 440 94 525 88 V100 C440 104 350 98 260 76 C170 54 90 52 0 62 Z" fill="var(--lavender)"/>
      <path d="M0 0 H525 V82 C440 88 350 80 260 56 C170 32 90 34 0 45 Z" fill="var(--royal)"/>
    </svg>
    <p class="holder-name">Elena Ward Hollis</p>
    <div class="front-brand">
      <p class="brand-name">Marlowe Hale</p>
      <p class="brand-line">FINE JEWELRY</p>
    </div>
    <address class="address" style="font-style:normal;">2280 Linden Avenue<br>Bayport, FL 32490</address>
    <ul class="contact">
      <li><b>p</b> : 555-014-2280</li>
      <li><b>e</b> : elena@marlowehalejewelry.com</li>
      <li><b>w</b> : www.marlowehalejewelry.com</li>
    </ul>
  </section>

  <section class="card card--white card-back" style="left:621px; top:73px;">
    <div class="back-brand">
      <p class="brand-name">Marlowe Hale</p>
      <p class="brand-line">FINE JEWELRY</p>
    </div>
    <p class="back-web">www.marlowehalejewelry.com</p>
  </section>

  <section class="card card--royal card-back" style="left:54px; top:445px;">
    <div class="back-brand">
      <p class="brand-name">Marlowe Hale</p>
      <p class="brand-line">FINE JEWELRY</p>
    </div>
    <p class="back-web">www.marlowehalejewelry.com</p>
  </section>

  <section class="card card--lavender card-back" style="left:622px; top:445px;">
    <div class="back-brand">
      <p class="brand-name">Marlowe Hale</p>
      <p class="brand-line">FINE JEWELRY</p>
    </div>
    <p class="back-web">www.marlowehalejewelry.com</p>
  </section>
</body>
</html>
```